Corvane Grid Works Ltd. -Website Design

We need a site design for a new company based in Toronto, Ontario called 'Corvane Grid Works Ltd.'

We provide Engineering services, Subsurface Utility Engineering services and Geospatial Data Management.

Our clients are typically Utilities (electric, gas, water/waste water, telcom) or contractors/consultants working on their behalf.

Our business model is new and we are the first to offer all three services to our clients; this allows us to provide value-added services from all three of our main offerings.

Target Market(s)

Field Supervisors, Managers, Directors, VP's at Utility companies

Industry/Entity Type

Business

Requirements
Must have
• -The landing page must clearly identify the 3 main business offerings allowing the user to easily navigate to each....Utility Engineering, GIS Data Management & Sub-surface Utility Engineering (SUE).

-Interactive contact page with integrated email

-based on existing logo design...
Nice to have
• -Ability to easily add/post news releases, updates, jobs, etc...

-Ability to integrate instructional YouTube video(s)

Should not have
• -Cannot be too cluttered....

```html
<!DOCTYPE html>
<html lang="en">
<head>
<meta charset="utf-8">
<title>Corvane Grid Works Ltd. – Utility Services</title>
<link rel="stylesheet" href="https://fonts.googleapis.com/css2?family=Cabin:wght@400;600&family=Special+Elite&family=Arimo:wght@400;700&display=swap">
<style>
:root{
  --parchment-warm:#e8b866;
  --parchment-mid:#f3dfae;
  --parchment-light:#fbf5e6;
  --ink-dark:#2c1a0c;
  --ink-brown:#5a2c0e;
  --text-rust:#a5552a;
  --accent-orange:#c2571c;
  --rule:#3b2410;
  --frame:#7a4a22;
  --footer:#c4652c;
  --field:#efe8d8;
  --body-text:#3a3a3a;
}
*{margin:0;padding:0;box-sizing:border-box}
html,body{width:923px;height:1200px;overflow:hidden}
body{
  position:relative;
  font-family:"Arimo",Arial,sans-serif;
  background:
    radial-gradient(ellipse 420px 700px at 0 200px, rgba(214,140,40,.55), transparent 70%),
    radial-gradient(ellipse 300px 500px at 923px 150px, rgba(200,130,40,.55), transparent 70%),
    linear-gradient(180deg, var(--parchment-warm) 0, var(--parchment-mid) 320px, var(--parchment-light) 820px, #fdf9ef 1140px);
}
.abs{position:absolute}
.brand{left:88px;top:32px;display:flex;align-items:center;gap:12px}
.brand-mark{width:62px;height:62px;background:var(--accent-orange)}
.brand-name{font-family:"Cabin",sans-serif;font-weight:600;font-size:28px;color:var(--body-text);line-height:1}
.main-nav{right:111px;top:78px;display:flex;font-family:"Cabin",sans-serif;font-size:17px;color:var(--ink-dark)}
.main-nav a{color:inherit;text-decoration:none;padding:0 12px;border-left:2px solid var(--ink-dark);line-height:20px}
.main-nav a:first-child{border-left:0}
.main-nav a:last-child{padding-right:0}
.rule{height:2px;background:linear-gradient(90deg,transparent,var(--rule) 4%,var(--rule) 96%,transparent)}
.featured-title{left:88px;top:176px;font-family:"Special Elite",cursive;font-weight:400;font-size:30px;line-height:32px;color:var(--ink-brown);letter-spacing:-1px}
.featured-text{left:89px;top:240px;width:352px;font-size:10px;line-height:17px;letter-spacing:-.1px;color:var(--text-rust)}
.featured-role{left:89px;top:321px;width:350px;white-space:nowrap;font-size:10.4px;letter-spacing:-.25px;font-weight:700;color:var(--ink-brown)}
.featured-photo{left:453px;top:157px;width:385px;height:190px;border:6px solid var(--frame);background:linear-gradient(180deg,#3f8fe0 0,#7cb6ec 55%,#c9e1f4 100%)}
.service{width:235px}
.service h2{font-weight:400;font-size:16px;line-height:20px;color:var(--ink-brown)}
.service .tagline{font-size:9px;color:var(--text-rust);margin-top:6px}
.service .plan{margin-top:12px;width:230px;height:147px;border:4px solid #fff;box-shadow:0 0 4px rgba(0,0,0,.2);background:linear-gradient(160deg,#6f8491,#566b78)}
.service ul{list-style:none;margin-top:11px}
.service li{position:relative;padding-left:19px;font-size:9.8px;letter-spacing:.5px;line-height:13px;color:var(--body-text);margin-bottom:5.4px}
.service li svg{position:absolute;left:0;top:2px}
.btn-more{width:125px;height:24px;border:1px solid #d8d2c6;border-radius:2px;background:linear-gradient(180deg,#f8f6f2,#e4e0d8);font-size:11px;color:var(--ink-brown);display:flex;align-items:center;justify-content:space-between;padding:0 6px 0 9px;text-decoration:none}
.block-title{font-size:11px;font-weight:400;color:var(--accent-orange);text-transform:uppercase;letter-spacing:-.2px}
.field{left:92px;width:184px;height:24px;background:var(--field);border:1px solid #e2d9c6;font-size:11px;color:#6b4a2c;padding:5px 8px}
.btn-submit{left:170px;top:1104px;width:94px;height:24px;border:1px solid #d8d2c6;background:linear-gradient(180deg,#fbfaf7,#e6e2da);font-size:11px;color:var(--ink-brown);text-align:center;line-height:22px}
.video{left:341px;top:954px;width:212px;height:129px;background:#000}
.about-text{left:606px;top:953px;width:232px;font-size:8.3px;line-height:12.6px;text-align:justify;color:#7a3010}
.site-footer{left:0;top:1140px;width:923px;height:60px;background:linear-gradient(90deg,#d27a3c,var(--footer) 40%,#b8561d);color:#fff;font-size:9.5px}
.site-footer .addr{left:89px;top:12px}
.site-footer .follow{left:89px;top:36px;display:flex;align-items:center;gap:7px}
.site-footer .follow span{width:18px;height:18px;background:#8a3a12;display:inline-block}
.site-footer .foot-nav{right:81px;top:12px;display:flex}
.site-footer .foot-nav a{color:#fff;text-decoration:none;padding:0 12px;border-left:1px solid #fff;line-height:10px}
.site-footer .foot-nav a:first-child{border-left:0}
.site-footer .foot-nav a:last-child{padding-right:0}
.site-footer .copy{right:81px;top:35px}
</style>
</head>
<body>

<header>
  <div class="abs brand"><span class="brand-mark"></span><span class="brand-name">Corvane Grid Works</span></div>
  <nav class="abs main-nav"><a href="#">home</a><a href="#">about</a><a href="#">services</a><a href="#">contact</a></nav>
</header>
<div class="abs rule" style="left:82px;top:132px;width:758px"></div>

<section>
  <h1 class="abs featured-title">FEATURED WORK</h1>
  <p class="abs featured-text">Lorem ipsum dolor sit amet, consectetuer adipiscing elit, sed diam nonummy nibh euismod tincidunt ut laoreet dolore magna aliquam erat volutpat. Ut wisi enim ad minim veniam, quis nostrud exerci tation ullamcorper suscipit lobortis nisl ut aliquip ex ea commodo consequat.</p>
  <p class="abs featured-role">Responsiblities: Lorem ipsum dolor sit amet, consectetuer adipiscing elit</p>
  <div class="abs featured-photo" role="img" aria-label="Photo of two business people shaking hands in front of wind turbines under a blue sky"></div>
</section>
<div class="abs rule" style="left:93px;top:374px;width:760px"></div>

<svg width="0" height="0" style="position:absolute"><defs><symbol id="bullet" viewBox="0 0 8 8"><path d="M1 1l3 3-3 3M4 1l3 3-3 3" fill="none" stroke="#5a2c0e" stroke-width="1.3"/></symbol></defs></svg>

<section class="abs service" style="left:90px;top:398px">
  <h2>Utility Engineering</h2>
  <p class="tagline">-------------Tagline------------</p>
  <div class="plan" role="img" aria-label="Site plan drawing of utility routes"></div>
  <ul>
    <li><svg width="7" height="7"><use href="#bullet"/></svg>Project Management</li>
    <li><svg width="7" height="7"><use href="#bullet"/></svg>Outside Plant Network Design</li>
    <li><svg width="7" height="7"><use href="#bullet"/></svg>Utility Design and Permitting</li>
    <li><svg width="7" height="7"><use href="#bullet"/></svg>Project Management</li>
    <li><svg width="7" height="7"><use href="#bullet"/></svg>Surveys and Mapping (GPS)</li>
    <li><svg width="7" height="7"><use href="#bullet"/></svg>Pole line design and attachment permitting (Pole Load Calculations)</li>
    <li><svg width="7" height="7"><use href="#bullet"/></svg>Specialty Permits for the Utility Industry (Railway, MTO, Conservation Authority)</li>
    <li><svg width="7" height="7"><use href="#bullet"/></svg>Manhole and Duct Bank Design.</li>
  </ul>
</section>

<section class="abs service" style="left:350px;top:398px">
  <h2>GIS Data Management</h2>
  <p class="tagline">-------------Tagline------------</p>
  <div class="plan" role="img" aria-label="Site plan drawing of utility routes"></div>
  <ul>
    <li><svg width="7" height="7"><use href="#bullet"/></svg>GIS Project Management;</li>
    <li><svg width="7" height="7"><use href="#bullet"/></svg>Records Conversion for GIS Systems;</li>
    <li><svg width="7" height="7"><use href="#bullet"/></svg>Landbase Data Management;</li>
    <li><svg width="7" height="7"><use href="#bullet"/></svg>Data Translation and Transformation Between File Formats;</li>
    <li><svg width="7" height="7"><use href="#bullet"/></svg>Hydro Asset Management using Geomark;</li>
    <li><svg width="7" height="7"><use href="#bullet"/></svg>Spatial Data Analysis &amp; Manipulation;</li>
    <li><svg width="7" height="7"><use href="#bullet"/></svg>Fibre Asset Management using Geomark &amp; LineTrace Software;</li>
    <li><svg width="7" height="7"><use href="#bullet"/></svg>Custom Cartographic Mapping;</li>
    <li><svg width="7" height="7"><use href="#bullet"/></svg>Engineering and Base Mapping using Geomark, DraftCore, PlotSphere;</li>
    <li><svg width="7" height="7"><use href="#bullet"/></svg>Geomark Customization &amp; Application Development</li>
    <li><svg width="7" height="7"><use href="#bullet"/></svg>Database Development.</li>
  </ul>
</section>

<section class="abs service" style="left:608px;top:398px">
  <h2>Sub-surface Utility Engineering</h2>
  <p class="tagline">-------------Tagline------------</p>
  <div class="plan" role="img" aria-label="Site plan drawing of utility routes"></div>
  <ul>
    <li><svg width="7" height="7"><use href="#bullet"/></svg>Project Management;</li>
    <li><svg width="7" height="7"><use href="#bullet"/></svg>Consulting;</li>
    <li><svg width="7" height="7"><use href="#bullet"/></svg>Surveying;</li>
    <li><svg width="7" height="7"><use href="#bullet"/></svg>CAD Processing of Results.</li>
  </ul>
</section>

<a class="abs btn-more" href="#" style="left:91px;top:863px">Learn More<svg width="16" height="6"><path d="M0 3h14M11 0.5l3.5 2.5-3.5 2.5" fill="none" stroke="#6b4a2c" stroke-width="0.8"/></svg></a>
<a class="abs btn-more" href="#" style="left:353px;top:863px">Learn More<svg width="16" height="6"><path d="M0 3h14M11 0.5l3.5 2.5-3.5 2.5" fill="none" stroke="#6b4a2c" stroke-width="0.8"/></svg></a>
<a class="abs btn-more" href="#" style="left:612px;top:863px">Learn More<svg width="16" height="6"><path d="M0 3h14M11 0.5l3.5 2.5-3.5 2.5" fill="none" stroke="#6b4a2c" stroke-width="0.8"/></svg></a>

<div class="abs rule" style="left:80px;top:907px;width:760px"></div>

<h3 class="abs block-title" style="left:90px;top:930px">Get in touch</h3>
<div class="abs field" style="top:954px">Full Name</div>
<div class="abs field" style="top:981px">Contact No.</div>
<div class="abs field" style="top:1009px">Email Id</div>
<div class="abs field" style="top:1037px;height:60px">Comments</div>
<div class="abs btn-submit">Submit</div>

<h3 class="abs block-title" style="left:341px;top:930px">Instructional Videos</h3>
<div class="abs video">
  <svg width="212" height="129" viewBox="0 0 212 129">
    <path d="M96 40v36l30-18z" fill="#d8d8d8"/>
    <rect x="0" y="118" width="212" height="11" fill="#1b1b1b"/>
    <rect x="0" y="117" width="212" height="1" fill="#444"/>
    <path d="M6 121v5M9 121v5" stroke="#aaa" stroke-width="1.2"/>
    <path d="M22 122h2l3-2v7l-3-2h-2z" fill="#aaa"/>
    <rect x="36" y="122" width="18" height="3" fill="#777"/>
    <rect x="168" y="121" width="6" height="5" fill="none" stroke="#aaa" stroke-width=".8"/>
    <rect x="180" y="121" width="8" height="5" fill="none" stroke="#aaa" stroke-width=".8"/>
    <rect x="194" y="120" width="10" height="7" fill="none" stroke="#aaa" stroke-width=".8"/>
  </svg>
</div>

<h3 class="abs block-title" style="left:606px;top:930px">About this website</h3>
<p class="abs about-text">"Lorem ipsum dolor sit amet, consectetur adipisicing elit, sed do eiusmod tempor incididunt ut labore et dolore magna aliqua. Ut enim ad minim veniam, quis nostrud exercitation ullamco laboris nisi ut aliquip ex ea commodo consequat. Duis aute irure dolor in reprehenderit in voluptate velit esse cillum dolore eu fugiat nulla pariatur.</p>

<footer class="abs site-footer">
  <p class="abs addr">418-2 Alder Crt, Toronto, ON M4B 2K7 T - 416.555.0142 F - 416.555.0143 info@corvanegrid.ca</p>
  <div class="abs follow">Follow Us On <span></span><span></span><span></span></div>
  <nav class="abs foot-nav"><a href="#">Home</a><a href="#">About</a><a href="#">Services</a><a href="#">Contact</a></nav>
  <p class="abs copy">© 2012 Corvanegrid.ca, All Rights Reserved.</p>
</footer>

</body>
</html>
```